We need a business card for our gym. We are a PowerCore affiliate in Decatur Georgie established 2008. Our company name is Rally Functional Fitness. PowerCore Building Prime Fitness. Instagram and website is @rallygym. Hashtags we use #rallywithheart #madetorally We want something similar to the the black and neon green design attached but a different color scheme. No neon colors. Are company colors are the same as the blue and white card attached. We are open to ideas as far as colors however - just no neon.

Contact Information for Business Card

Rally Functional Fitness
472 Halvern Drive
Decatur GA 30041
Phone 404.555.0187 Website www.rallygym.example

Font styles to use
Other font styles liked:
• Futura Extra Bold Condensed

Colors

Designer to choose colors to be used in the design.

Requirements
Must have
• Our primary font we typically use for our name is Futura Extra Bold Condensed
Nice to have
• I attached a card from that is black and neon green from Zorva that we would like something similar. The blue and white is more similar to our colors. We also use have used black and white in the past. We use the chevrons as out logo. We are a PowerCore affiliate so I included a logo from them as well that may or may not be used on the card. Our instagram is @rallygym hashtags #madetorally #rallywithheart
Should not have
• No neon colors

```html
<!DOCTYPE html>
<html lang="en">
<head>
<meta charset="utf-8">
<title>Rally Functional Fitness – Business Card</title>
<link href="https://fonts.googleapis.com/css2?family=Anton&family=Oswald:wght@500;600&family=Montserrat:wght@400;500&display=swap" rel="stylesheet">
<style>
  :root {
    --bg: #2a2a2a;
    --card: #1d1d1e;
    --gloss: #3d3f3c;
    --gloss-light: #55574f;
    --ink-soft: #4b4b4b;
    --ink-contact: #a3a3a3;
    --rule: #555555;
  }
  * { box-sizing: border-box; margin: 0; padding: 0; }
  html, body {
    width: 1200px; height: 901px; overflow: hidden;
    background: var(--bg);
  }
  .stage { position: relative; width: 1200px; height: 901px; }
  .card {
    position: absolute; left: 290px;
    width: 620px; height: 354px;
    background: var(--card);
    box-shadow: 0 10px 30px rgba(0,0,0,.45);
  }
  .card--front { top: 76px; }
  .card--back  { top: 470px; }

  /* Front */
  .brand {
    position: absolute; left: 0; right: 0; top: 108px;
    text-align: center; color: var(--gloss-light);
    font-family: "Anton", sans-serif; font-weight: 400;
    text-transform: uppercase; line-height: 1;
  }
  .brand__name { display: block; font-size: 96px; letter-spacing: 2px; }
  .brand__tag  { display: block; font-size: 31px; letter-spacing: 2px; margin-top: 6px; }

  /* Back */
  .identity {
    position: absolute; top: 118px; right: 338px;
    text-align: right;
  }
  .identity__name {
    font-family: "Oswald", sans-serif; font-weight: 600;
    font-size: 34px; letter-spacing: 1px; color: var(--gloss-light);
    text-transform: uppercase; line-height: 1.05;
  }
  .identity__role {
    font-family: "Montserrat", sans-serif; font-weight: 400;
    font-size: 19px; letter-spacing: 1px; color: var(--ink-soft);
    text-transform: uppercase; margin-top: 2px;
  }
  .divider {
    position: absolute; left: 300px; top: 120px;
    width: 1px; height: 92px; background: var(--rule);
  }
  .contact {
    position: absolute; left: 324px; top: 122px;
    list-style: none;
    font-family: "Montserrat", sans-serif; font-weight: 500;
    font-size: 19px; color: var(--ink-contact);
  }
  .contact li { display: flex; align-items: center; gap: 8px; height: 30px; }
  .contact svg { width: 16px; height: 16px; fill: var(--ink-contact); flex: none; }
  .address {
    position: absolute; left: 0; right: 0; bottom: 46px;
    text-align: center;
    font-family: "Montserrat", sans-serif; font-weight: 500;
    font-size: 20px; color: var(--ink-soft);
  }
</style>
</head>
<body>
<main class="stage">
  <section class="card card--front" aria-label="Card front">
    <h1 class="brand">
      <span class="brand__name">Rally</span>
      <span class="brand__tag">Functional Fitness</span>
    </h1>
  </section>

  <section class="card card--back" aria-label="Card back">
    <div class="identity">
      <p class="identity__name">Dorian Castwell</p>
      <p class="identity__role">Expert Coaches</p>
    </div>
    <div class="divider"></div>
    <ul class="contact">
      <li>
        <svg viewBox="0 0 24 24" aria-hidden="true"><path d="M6.6 10.8a15.1 15.1 0 0 0 6.6 6.6l2.2-2.2c.3-.3.7-.4 1-.2 1.1.4 2.3.6 3.6.6.6 0 1 .4 1 1V20c0 .6-.4 1-1 1A17 17 0 0 1 3 4c0-.6.4-1 1-1h3.5c.6 0 1 .4 1 1 0 1.3.2 2.5.6 3.6.1.3 0 .7-.2 1z"/></svg>
        404.555.0187
      </li>
      <li>
        <svg viewBox="0 0 24 24" aria-hidden="true"><path d="M2 5h20v14H2z M3.5 6.5 12 13l8.5-6.5" fill="none" stroke="#a3a3a3" stroke-width="2"/></svg>
        info@rallygym.example
      </li>
      <li>
        <svg viewBox="0 0 24 24" aria-hidden="true"><circle cx="12" cy="12" r="10"/><path d="M2 12h20M12 2c3 3 3 17 0 20M12 2c-3 3-3 17 0 20" fill="none" stroke="#1d1d1e" stroke-width="1.6"/></svg>
        www.rallygym.example
      </li>
    </ul>
    <p class="address">472 Halvern Drive, Decatur GA 30041</p>
  </section>
</main>
</body>
</html>
```